Brainwave state designs for neurofeedback report

Design ORIGINAL graphics that correspond with existing colors and shapes for Halo Prism Grid of Stillness & Halo Prism Rhythm Panel for "Normal", "Bright Harbor", "Summit Tide" etc... patterns. You can change the shape of the white outline to be more modern looking. Perhaps you can also use white background with black outline. The frequency bars (can be more ordered) but keep the general shape of the outline.

• An original flair. Modern. Neurotechish
• Do not copy the design. Add your original ideas. Choose a font that complements the design.

```html
<!DOCTYPE html>
<html lang="en">
<head>
<meta charset="utf-8">
<title>Halo Prism Grid of Stillness</title>
<link href="https://fonts.googleapis.com/css2?family=Sora:wght@400;600;700&family=JetBrains+Mono:wght@500;700&display=swap" rel="stylesheet">
<style>
  :root{
    --ink:#101318;
    --muted:#6b7280;
    --grid:#e1e4e8;
    --guide:#e0454a;
    --gamma:#d6282b;
    --beta-hi:#f0543a;
    --beta-mid:#f26a35;
    --beta-lo:#f7913a;
    --beta-edge:#f9a93a;
    --alpha-lo:#5a9a48;
    --alpha:#2e7d3a;
    --alpha-deep:#1f6e35;
    --theta-hi:#5b9bd5;
    --theta:#6a7fcb;
    --theta-lo:#7d6bbd;
    --delta:#8b55b0;
    --delta-mid:#9a47a3;
    --delta-lo:#9b3c9b;
    --label-beta:#f15a2b;
    --label-alpha:#1a8a47;
    --label-theta:#5b8bd0;
    --label-delta:#9b2f9a;
  }
  html,body{margin:0;padding:0;width:993px;height:1200px;overflow:hidden;background:#fff;}
  .board{display:block;width:993px;height:1200px;font-family:"Sora",sans-serif;}
  .title{font-size:19px;font-weight:600;fill:var(--ink);text-anchor:middle;letter-spacing:1.5px;}
  .band-label{font-size:12.5px;font-weight:700;text-anchor:middle;letter-spacing:.6px;}
  .band-beta{fill:var(--label-beta);} .band-alpha{fill:var(--label-alpha);}
  .band-theta{fill:var(--label-theta);} .band-delta{fill:var(--label-delta);}
  .guide{stroke:var(--guide);stroke-width:1;stroke-dasharray:6 5;opacity:.8;}
  .gridline{stroke:var(--grid);stroke-width:1;}
  .zero{stroke:#c7ccd3;stroke-width:1;}
  .contour{fill:none;stroke:var(--ink);stroke-width:1.6;stroke-linecap:round;}
  .node{fill:#fff;stroke:var(--ink);stroke-width:1.4;}
  .freq{font-family:"JetBrains Mono",monospace;font-size:11px;font-weight:700;text-anchor:middle;fill:var(--ink);}
  .freq-sm{font-family:"JetBrains Mono",monospace;font-size:6.5px;font-weight:700;text-anchor:middle;fill:var(--ink);}
  .freq-xs{font-family:"JetBrains Mono",monospace;font-size:5.5px;font-weight:700;text-anchor:middle;fill:var(--ink);}
  .axis{font-family:"JetBrains Mono",monospace;font-size:9.5px;fill:var(--muted);text-anchor:middle;}
  .axis-sm{font-family:"JetBrains Mono",monospace;font-size:6.5px;fill:var(--muted);text-anchor:middle;}
  .axis-name{font-size:10px;fill:var(--muted);text-anchor:middle;letter-spacing:1px;}
  .axis-name-sm{font-size:6.5px;fill:var(--muted);text-anchor:middle;letter-spacing:.8px;}
  .caption{font-size:12px;font-weight:600;fill:var(--ink);text-anchor:middle;}
  .halo{fill:url(#halo);}
  .quiet{stroke:var(--gamma);stroke-width:1.4;stroke-dasharray:2 2;}
  .g{fill:var(--gamma);} .b1{fill:var(--beta-hi);} .b2{fill:var(--beta-mid);} .b3{fill:var(--beta-lo);} .b4{fill:var(--beta-edge);}
  .a1{fill:var(--alpha-lo);} .a2{fill:var(--alpha);} .a3{fill:var(--alpha-deep);} .a3l{fill:var(--alpha-lo);}
  .t1{fill:var(--theta-hi);} .t2{fill:var(--theta);} .t3{fill:var(--theta-lo);}
  .d1{fill:var(--delta);} .d2{fill:var(--delta-mid);} .d3{fill:var(--delta-lo);}
</style>
</head>
<body>
<svg class="board" viewBox="0 0 993 1200" xmlns="http://www.w3.org/2000/svg">
  <defs>
    <linearGradient id="spectrum" x1="0" y1="0" x2="0" y2="1">
      <stop offset="0" stop-color="#f0543a"/>
      <stop offset=".28" stop-color="#f9a93a"/>
      <stop offset=".45" stop-color="#5a9a48"/>
      <stop offset=".55" stop-color="#1f7a3a"/>
      <stop offset=".72" stop-color="#5b7fa8"/>
      <stop offset=".85" stop-color="#6a7fcb"/>
      <stop offset="1" stop-color="#9b2f9a"/>
    </linearGradient>
    <linearGradient id="ice" x1="0" y1="0" x2="0" y2="1">
      <stop offset="0" stop-color="#3a3f46"/>
      <stop offset=".34" stop-color="#6b7785"/>
      <stop offset=".41" stop-color="#d3dbe2"/>
      <stop offset=".5" stop-color="#3c4a57"/>
      <stop offset="1" stop-color="#1d2026"/>
    </linearGradient>
    <radialGradient id="halo" cx=".5" cy=".5" r=".5">
      <stop offset="0" stop-color="#eceef1"/>
      <stop offset="1" stop-color="#f6f7f8"/>
    </radialGradient>
  </defs>

  <!-- Grid of stillness -->
  <text class="title" x="496" y="72">THE HALO PRISM GRID OF STILLNESS</text>

  <g class="spectrum-key">
    <rect x="46" y="120" width="8" height="288" rx="4" fill="url(#spectrum)"/>
    <text class="band-label band-beta" x="150" y="162">BETA</text>
    <text class="band-label band-beta" x="150" y="178">CONSCIOUS MIND</text>
    <text class="band-label band-alpha" x="150" y="242">ALPHA</text>
    <text class="band-label band-alpha" x="150" y="258">BRIDGE</text>
    <text class="band-label band-theta" x="150" y="303">THETA</text>
    <text class="band-label band-theta" x="150" y="319">SUBCONSCIOUS MIND</text>
    <text class="band-label band-delta" x="150" y="364">DELTA</text>
    <text class="band-label band-delta" x="150" y="380">UNCONSCIOUS MIND</text>
  </g>

  <rect x="650" y="94" width="288" height="364" rx="14" fill="url(#ice)" role="img" aria-label="Iceberg above and below the waterline"/>

  <g class="band-guides">
    <line class="guide" x1="66" y1="216" x2="938" y2="216"/>
    <line class="guide" x1="66" y1="278" x2="938" y2="278"/>
    <line class="guide" x1="66" y1="339" x2="938" y2="339"/>
  </g>

  <g class="main-chart" transform="translate(430,124)">
    <g class="grid">
      <line class="gridline" x1="-165" y1="-10" x2="-165" y2="278"/><line class="gridline" x1="-136" y1="-10" x2="-136" y2="278"/>
      <line class="gridline" x1="-107" y1="-10" x2="-107" y2="278"/><line class="gridline" x1="-78" y1="-10" x2="-78" y2="278"/>
      <line class="gridline" x1="-49" y1="-10" x2="-49" y2="278"/><line class="zero" x1="-20" y1="-10" x2="-20" y2="278"/>
      <line class="zero" x1="20" y1="-10" x2="20" y2="278"/><line class="gridline" x1="49" y1="-10" x2="49" y2="278"/>
      <line class="gridline" x1="78" y1="-10" x2="78" y2="278"/><line class="gridline" x1="107" y1="-10" x2="107" y2="278"/>
      <line class="gridline" x1="136" y1="-10" x2="136" y2="278"/><line class="gridline" x1="165" y1="-10" x2="165" y2="278"/>
    </g>
    <g class="bars">
      <rect class="b1" x="-42" y="-5.5" width="22" height="11" rx="5.5"/><rect class="b1" x="20" y="-5.5" width="31" height="11" rx="5.5"/>
      <rect class="b1" x="-39" y="15" width="19" height="11" rx="5.5"/><rect class="b1" x="20" y="15" width="22" height="11" rx="5.5"/>
      <rect class="b2" x="-52" y="35.5" width="32" height="11" rx="5.5"/><rect class="b2" x="20" y="35.5" width="31" height="11" rx="5.5"/>
      <rect class="b3" x="-65" y="56" width="45" height="11" rx="5.5"/><rect class="b3" x="20" y="56" width="34" height="11" rx="5.5"/>
      <rect class="b4" x="-69" y="76.5" width="49" height="11" rx="5.5"/><rect class="b4" x="20" y="76.5" width="42" height="11" rx="5.5"/>
      <rect class="a1" x="-69" y="97" width="49" height="11" rx="5.5"/><rect class="a1" x="20" y="97" width="52" height="11" rx="5.5"/>
      <rect class="a2" x="-106" y="117.5" width="86" height="11" rx="5.5"/><rect class="a2" x="20" y="117.5" width="101" height="11" rx="5.5"/>
      <rect class="a3" x="-94" y="138" width="74" height="11" rx="5.5"/><rect class="a3" x="20" y="138" width="101" height="11" rx="5.5"/>
      <rect class="t1" x="-57" y="158.5" width="37" height="11" rx="5.5"/><rect class="t1" x="20" y="158.5" width="31" height="11" rx="5.5"/>
      <rect class="t2" x="-67" y="179" width="47" height="11" rx="5.5"/><rect class="t2" x="20" y="179" width="53" height="11" rx="5.5"/>
      <rect class="t3" x="-52" y="199.5" width="32" height="11" rx="5.5"/><rect class="t3" x="20" y="199.5" width="38" height="11" rx="5.5"/>
      <rect class="d1" x="-82" y="220" width="62" height="11" rx="5.5"/><rect class="d1" x="20" y="220" width="53" height="11" rx="5.5"/>
      <rect class="d2" x="-73" y="240.5" width="53" height="11" rx="5.5"/><rect class="d2" x="20" y="240.5" width="44" height="11" rx="5.5"/>
      <rect class="d3" x="-36" y="261" width="16" height="11" rx="5.5"/><rect class="d3" x="20" y="261" width="16" height="11" rx="5.5"/>
    </g>
    <g class="labels">
      <text class="freq" y="4">38</text><text class="freq" y="24.5">30</text><text class="freq" y="45">24</text>
      <text class="freq" y="65.5">19</text><text class="freq" y="86">15</text><text class="freq" y="106.5">12.5</text>
      <text class="freq" y="127">10.5</text><text class="freq" y="147.5">9</text><text class="freq" y="168">7.5</text>
      <text class="freq" y="188.5">6</text><text class="freq" y="209">4</text><text class="freq" y="229.5">3</text>
      <text class="freq" y="250">1.5</text><text class="freq" y="270.5">0.75</text>
    </g>
    <path class="contour" d="M-48,-8 C-52,26 -70,61 -80,82 C-92,104 -130,108 -128,126 C-126,146 -85,151 -72,166 C-64,178 -82,190 -74,202 C-66,214 -98,218 -96,236 C-94,254 -70,268 -48,276"/>
    <path class="contour" d="M56,-8 C60,26 70,61 78,82 C90,104 136,108 136,128 C136,148 80,151 66,166 C56,178 96,188 88,202 C80,214 90,218 90,236 C90,254 70,268 48,276"/>
    <circle class="node" cx="-48" cy="-8" r="2.6"/><circle class="node" cx="-48" cy="276" r="2.6"/>
    <circle class="node" cx="56" cy="-8" r="2.6"/><circle class="node" cx="48" cy="276" r="2.6"/>
    <circle class="node" cx="-128" cy="126" r="2.6"/><circle class="node" cx="136" cy="128" r="2.6"/>
    <g class="axis-row">
      <text class="axis" x="-165" y="298">15</text><text class="axis" x="-136" y="298">12</text><text class="axis" x="-107" y="298">9</text>
      <text class="axis" x="-78" y="298">6</text><text class="axis" x="-49" y="298">3</text><text class="axis" x="49" y="298">3</text>
      <text class="axis" x="78" y="298">6</text><text class="axis" x="107" y="298">9</text><text class="axis" x="136" y="298">12</text>
      <text class="axis" x="165" y="298">15</text>
      <text class="axis-name" x="0" y="316">sEMG</text>
    </g>
  </g>

  <!-- Rhythm panel -->
  <text class="title" x="496" y="552">THE HALO PRISM RHYTHM PANEL</text>
  <text class="title" x="496" y="576">(BARS/PATTERNS) DYNAMICS</text>

  <!-- Ordinary -->
  <g class="pattern pattern-ordinary" transform="translate(182,628)">
    <circle class="halo" cx="0" cy="72" r="72" role="img" aria-label="Brain illustration"/>
    <line class="gridline" x1="-101" y1="-8" x2="-101" y2="142"/><line class="zero" x1="-11" y1="-8" x2="-11" y2="142"/>
    <line class="zero" x1="11" y1="-8" x2="11" y2="142"/><line class="gridline" x1="101" y1="-8" x2="101" y2="142"/>
    <rect class="b1" x="-77" y="-3.5" width="66" height="7" rx="3.5"/><rect class="b1" x="11" y="-3.5" width="66" height="7" rx="3.5"/>
    <rect class="b1" x="-94" y="7" width="83" height="7" rx="3.5"/><rect class="b1" x="11" y="7" width="68" height="7" rx="3.5"/>
    <rect class="b2" x="-65" y="17.5" width="54" height="7" rx="3.5"/><rect class="b2" x="11" y="17.5" width="54" height="7" rx="3.5"/>
    <rect class="b3" x="-54" y="28" width="43" height="7" rx="3.5"/><rect class="b3" x="11" y="28" width="43" height="7" rx="3.5"/>
    <rect class="b4" x="-50" y="38.5" width="39" height="7" rx="3.5"/><rect class="b4" x="11" y="38.5" width="39" height="7" rx="3.5"/>
    <rect class="a1" x="-40" y="49" width="29" height="7" rx="3.5"/><rect class="a1" x="11" y="49" width="30" height="7" rx="3.5"/>
    <rect class="a2" x="-35" y="59.5" width="24" height="7" rx="3.5"/><rect class="a2" x="11" y="59.5" width="21" height="7" rx="3.5"/>
    <rect class="a3" x="-32" y="70" width="21" height="7" rx="3.5"/><rect class="a3" x="11" y="70" width="21" height="7" rx="3.5"/>
    <rect class="t1" x="-28" y="80.5" width="17" height="7" rx="3.5"/><rect class="t1" x="11" y="80.5" width="17" height="7" rx="3.5"/>
    <rect class="t2" x="-30" y="91" width="19" height="7" rx="3.5"/><rect class="t2" x="11" y="91" width="21" height="7" rx="3.5"/>
    <rect class="t3" x="-32" y="101.5" width="21" height="7" rx="3.5"/><rect class="t3" x="11" y="101.5" width="24" height="7" rx="3.5"/>
    <rect class="d1" x="-30" y="112" width="19" height="7" rx="3.5"/><rect class="d1" x="11" y="112" width="19" height="7" rx="3.5"/>
    <rect class="d2" x="-39" y="122.5" width="28" height="7" rx="3.5"/><rect class="d2" x="11" y="122.5" width="30" height="7" rx="3.5"/>
    <rect class="d3" x="-52" y="133" width="41" height="7" rx="3.5"/><rect class="d3" x="11" y="133" width="41" height="7" rx="3.5"/>
    <text class="freq-sm" y="2.5">38</text><text class="freq-sm" y="13">30</text><text class="freq-sm" y="23.5">24</text><text class="freq-sm" y="34">19</text><text class="freq-sm" y="44.5">15</text><text class="freq-sm" y="55">12.5</text><text class="freq-sm" y="65.5">10.5</text><text class="freq-sm" y="76">9</text><text class="freq-sm" y="86.5">7.5</text><text class="freq-sm" y="97">6</text><text class="freq-sm" y="107.5">4</text><text class="freq-sm" y="118">3</text><text class="freq-sm" y="128.5">1.5</text><text class="freq-sm" y="139">0.75</text>
    <path class="contour" d="M-100,-6 C-104,25 -52,35 -46,60 C-42,90 -50,110 -64,140"/>
    <path class="contour" d="M100,-6 C104,25 52,35 46,60 C42,90 50,110 64,140"/>
    <circle class="node" cx="-100" cy="-6" r="2"/><circle class="node" cx="-64" cy="140" r="2"/><circle class="node" cx="100" cy="-6" r="2"/><circle class="node" cx="64" cy="140" r="2"/>
    <text class="axis-sm" x="-101" y="156">10µV</text><text class="axis-sm" x="-11" y="156">0µV</text><text class="axis-sm" x="11" y="156">0µV</text><text class="axis-sm" x="101" y="156">10µV</text>
    <text class="axis-name-sm" y="168">sEMG</text>
    <text class="caption" y="190">Ordinary Mind</text>
  </g>

  <!-- Bright Harbor -->
  <g class="pattern pattern-bright-harbor" transform="translate(489,628)">
    <circle class="halo" cx="0" cy="72" r="72" role="img" aria-label="Brain illustration"/>
    <line class="gridline" x1="-101" y1="-8" x2="-101" y2="142"/><line class="gridline" x1="-56" y1="-8" x2="-56" y2="142"/>
    <line class="zero" x1="-11" y1="-8" x2="-11" y2="142"/><line class="zero" x1="11" y1="-8" x2="11" y2="142"/>
    <line class="gridline" x1="56" y1="-8" x2="56" y2="142"/><line class="gridline" x1="101" y1="-8" x2="101" y2="142"/>
    <rect class="b1" x="-31" y="-3.5" width="20" height="7" rx="3.5"/><rect class="b1" x="11" y="-3.5" width="12" height="7" rx="3.5"/>
    <rect class="b1" x="-32" y="7" width="21" height="7" rx="3.5"/><rect class="b1" x="11" y="7" width="13" height="7" rx="3.5"/>
    <rect class="b2" x="-36" y="17.5" width="25" height="7" rx="3.5"/><rect class="b2" x="11" y="17.5" width="21" height="7" rx="3.5"/>
    <rect class="b3" x="-43" y="28" width="32" height="7" rx="3.5"/><rect class="b3" x="11" y="28" width="28" height="7" rx="3.5"/>
    <rect class="b4" x="-43" y="38.5" width="32" height="7" rx="3.5"/><rect class="b4" x="11" y="38.5" width="38" height="7" rx="3.5"/>
    <rect class="a1" x="-49" y="49" width="38" height="7" rx="3.5"/><rect class="a1" x="11" y="49" width="54" height="7" rx="3.5"/>
    <rect class="a1" x="-72" y="59.5" width="61" height="7" rx="3.5"/><rect class="a1" x="11" y="59.5" width="60" height="7" rx="3.5"/>
    <rect class="a3" x="-117" y="70" width="106" height="7" rx="3.5"/><rect class="a3" x="11" y="70" width="95" height="7" rx="3.5"/>
    <rect class="t1" x="-45" y="80.5" width="34" height="7" rx="3.5"/><rect class="t1" x="11" y="80.5" width="36" height="7" rx="3.5"/>
    <rect class="t2" x="-50" y="91" width="39" height="7" rx="3.5"/><rect class="t2" x="11" y="91" width="39" height="7" rx="3.5"/>
    <rect class="t3" x="-42" y="101.5" width="31" height="7" rx="3.5"/><rect class="t3" x="11" y="101.5" width="31" height="7" rx="3.5"/>
    <rect class="d1" x="-45" y="112" width="34" height="7" rx="3.5"/><rect class="d1" x="11" y="112" width="31" height="7" rx="3.5"/>
    <rect class="d2" x="-44" y="122.5" width="33" height="7" rx="3.5"/><rect class="d2" x="11" y="122.5" width="45" height="7" rx="3.5"/>
    <rect class="d3" x="-70" y="133" width="59" height="7" rx="3.5"/><rect class="d3" x="11" y="133" width="32" height="7" rx="3.5"/>
    <text class="freq-sm" y="2.5">38</text><text class="freq-sm" y="13">30</text><text class="freq-sm" y="23.5">24</text><text class="freq-sm" y="34">19</text><text class="freq-sm" y="44.5">15</text><text class="freq-sm" y="55">12.5</text><text class="freq-sm" y="65.5">10.5</text><text class="freq-sm" y="76">9</text><text class="freq-sm" y="86.5">7.5</text><text class="freq-sm" y="97">6</text><text class="freq-sm" y="107.5">4</text><text class="freq-sm" y="118">3</text><text class="freq-sm" y="128.5">1.5</text><text class="freq-sm" y="139">0.75</text>
    <path class="contour" d="M-60,-8 C-62,30 -70,50 -95,55 C-130,60 -150,65 -130,78 C-110,86 -80,84 -72,94 C-62,110 -72,126 -90,140"/>
    <path class="contour" d="M40,-8 C45,20 75,35 95,55 C105,65 140,65 128,80 C115,88 80,88 72,100 C64,115 72,130 80,140"/>
    <circle class="node" cx="-60" cy="-8" r="2"/><circle class="node" cx="-90" cy="140" r="2"/><circle class="node" cx="40" cy="-8" r="2"/><circle class="node" cx="80" cy="140" r="2"/>
    <text class="axis-sm" x="-101" y="156">10µV</text><text class="axis-sm" x="-56" y="156">5µV</text><text class="axis-sm" x="-11" y="156">0µV</text><text class="axis-sm" x="11" y="156">0µV</text><text class="axis-sm" x="56" y="156">5µV</text><text class="axis-sm" x="101" y="156">10µV</text>
    <text class="axis-name-sm" y="168">sEMG</text>
    <text class="caption" y="190">Bright Harbor</text>
  </g>

  <!-- Summit Tide -->
  <g class="pattern pattern-summit-tide" transform="translate(794,628)">
    <circle class="halo" cx="0" cy="72" r="72" role="img" aria-label="Brain illustration"/>
    <line class="gridline" x1="-101" y1="-8" x2="-101" y2="142"/><line class="gridline" x1="-56" y1="-8" x2="-56" y2="142"/>
    <line class="zero" x1="-11" y1="-8" x2="-11" y2="142"/><line class="zero" x1="11" y1="-8" x2="11" y2="142"/>
    <line class="gridline" x1="56" y1="-8" x2="56" y2="142"/><line class="gridline" x1="101" y1="-8" x2="101" y2="142"/>
    <rect class="b1" x="-43" y="-3.5" width="32" height="7" rx="3.5"/><rect class="b1" x="11" y="-3.5" width="37" height="7" rx="3.5"/>
    <rect class="b1" x="-31" y="7" width="20" height="7" rx="3.5"/><rect class="b1" x="11" y="7" width="65" height="7" rx="3.5"/>
    <rect class="b2" x="-50" y="17.5" width="39" height="7" rx="3.5"/><rect class="b2" x="11" y="17.5" width="60" height="7" rx="3.5"/>
    <rect class="b3" x="-63" y="28" width="52" height="7" rx="3.5"/><rect class="b3" x="11" y="28" width="54" height="7" rx="3.5"/>
    <rect class="b4" x="-48" y="38.5" width="37" height="7" rx="3.5"/><rect class="b4" x="11" y="38.5" width="49" height="7" rx="3.5"/>
    <rect class="a2" x="-57" y="49" width="46" height="7" rx="3.5"/><rect class="a2" x="11" y="49" width="66" height="7" rx="3.5"/>
    <rect class="a2" x="-89" y="59.5" width="78" height="7" rx="3.5"/><rect class="a2" x="11" y="59.5" width="78" height="7" rx="3.5"/>
    <rect class="a3l" x="-66" y="70" width="55" height="7" rx="3.5"/><rect class="a3l" x="11" y="70" width="106" height="7" rx="3.5"/>
    <rect class="t1" x="-60" y="80.5" width="49" height="7" rx="3.5"/><rect class="t1" x="11" y="80.5" width="50" height="7" rx="3.5"/>
    <rect class="t2" x="-60" y="91" width="49" height="7" rx="3.5"/><rect class="t2" x="11" y="91" width="52" height="7" rx="3.5"/>
    <rect class="t3" x="-53" y="101.5" width="42" height="7" rx="3.5"/><rect class="t3" x="11" y="101.5" width="64" height="7" rx="3.5"/>
    <rect class="d1" x="-42" y="112" width="31" height="7" rx="3.5"/><rect class="d1" x="11" y="112" width="48" height="7" rx="3.5"/>
    <rect class="d2" x="-57" y="122.5" width="46" height="7" rx="3.5"/><rect class="d2" x="11" y="122.5" width="41" height="7" rx="3.5"/>
    <rect class="d3" x="-37" y="133" width="26" height="7" rx="3.5"/><rect class="d3" x="11" y="133" width="32" height="7" rx="3.5"/>
    <text class="freq-sm" y="2.5">38</text><text class="freq-sm" y="13">30</text><text class="freq-sm" y="23.5">24</text><text class="freq-sm" y="34">19</text><text class="freq-sm" y="44.5">15</text><text class="freq-sm" y="55">12.5</text><text class="freq-sm" y="65.5">10.5</text><text class="freq-sm" y="76">9</text><text class="freq-sm" y="86.5">7.5</text><text class="freq-sm" y="97">6</text><text class="freq-sm" y="107.5">4</text><text class="freq-sm" y="118">3</text><text class="freq-sm" y="128.5">1.5</text><text class="freq-sm" y="139">0.75</text>
    <path class="contour" d="M-70,-14 C-120,20 -132,90 -95,145"/>
    <path class="contour" d="M80,-24 C135,15 140,100 95,130"/>
    <circle class="node" cx="-70" cy="-14" r="2"/><circle class="node" cx="-95" cy="145" r="2"/><circle class="node" cx="80" cy="-24" r="2"/><circle class="node" cx="95" cy="130" r="2"/>
    <text class="axis-sm" x="-101" y="156">10µV</text><text class="axis-sm" x="-56" y="156">5µV</text><text class="axis-sm" x="-11" y="156">0µV</text><text class="axis-sm" x="11" y="156">0µV</text><text class="axis-sm" x="56" y="156">5µV</text><text class="axis-sm" x="101" y="156">10µV</text>
    <text class="axis-name-sm" y="168">sEMG</text>
    <text class="caption" y="190">Summit Tide</text>
  </g>

  <!-- Unknown state -->
  <g class="pattern pattern-unknown" transform="translate(205,905)">
    <circle class="halo" cx="0" cy="72" r="62" role="img" aria-label="Brain illustration"/>
    <line class="gridline" x1="-84" y1="-8" x2="-84" y2="140"/><line class="gridline" x1="-46.5" y1="-8" x2="-46.5" y2="140"/>
    <line class="zero" x1="-9" y1="-8" x2="-9" y2="140"/><line class="zero" x1="9" y1="-8" x2="9" y2="140"/>
    <line class="gridline" x1="46.5" y1="-8" x2="46.5" y2="140"/><line class="gridline" x1="84" y1="-8" x2="84" y2="140"/>
    <line class="quiet" x1="-10" y1="-4" x2="-10" y2="36"/><line class="quiet" x1="10" y1="-4" x2="10" y2="36"/>
    <rect class="b1" x="-14" y="37.5" width="5" height="5" rx="2.5"/><rect class="b1" x="9" y="37.5" width="6" height="5" rx="2.5"/>
    <rect class="b2" x="-15" y="45.5" width="6" height="5" rx="2.5"/><rect class="b2" x="9" y="45.5" width="6" height="5" rx="2.5"/>
    <rect class="b3" x="-26" y="53.5" width="17" height="5" rx="2.5"/><rect class="b3" x="9" y="53.5" width="12" height="5" rx="2.5"/>
    <rect class="b4" x="-33" y="61.5" width="24" height="5" rx="2.5"/><rect class="b4" x="9" y="61.5" width="20" height="5" rx="2.5"/>
    <rect class="a2" x="-38" y="69.5" width="29" height="5" rx="2.5"/><rect class="a2" x="9" y="69.5" width="25" height="5" rx="2.5"/>
    <rect class="a2" x="-56" y="77.5" width="47" height="5" rx="2.5"/><rect class="a2" x="9" y="77.5" width="23" height="5" rx="2.5"/>
    <rect class="a3l" x="-45" y="85.5" width="36" height="5" rx="2.5"/><rect class="a3l" x="9" y="85.5" width="49" height="5" rx="2.5"/>
    <rect class="t1" x="-52" y="93.5" width="43" height="5" rx="2.5"/><rect class="t1" x="9" y="93.5" width="41" height="5" rx="2.5"/>
    <rect class="t2" x="-56" y="101.5" width="47" height="5" rx="2.5"/><rect class="t2" x="9" y="101.5" width="42" height="5" rx="2.5"/>
    <rect class="t3" x="-62" y="109.5" width="53" height="5" rx="2.5"/><rect class="t3" x="9" y="109.5" width="50" height="5" rx="2.5"/>
    <rect class="d1" x="-98" y="117.5" width="89" height="5" rx="2.5"/><rect class="d1" x="9" y="117.5" width="59" height="5" rx="2.5"/>
    <rect class="d2" x="-112" y="125.5" width="103" height="5" rx="2.5"/><rect class="d2" x="9" y="125.5" width="55" height="5" rx="2.5"/>
    <rect class="d3" x="-115" y="133.5" width="106" height="5" rx="2.5"/><rect class="d3" x="9" y="133.5" width="57" height="5" rx="2.5"/>
    <text class="freq-xs" y="2">79</text><text class="freq-xs" y="10">69</text><text class="freq-xs" y="18">59</text><text class="freq-xs" y="26">49</text><text class="freq-xs" y="34">38</text><text class="freq-xs" y="42">30</text><text class="freq-xs" y="50">24</text><text class="freq-xs" y="58">19</text><text class="freq-xs" y="66">15</text><text class="freq-xs" y="74">12.5</text><text class="freq-xs" y="82">10.5</text><text class="freq-xs" y="90">9</text><text class="freq-xs" y="98">7.5</text><text class="freq-xs" y="106">6</text><text class="freq-xs" y="114">4</text><text class="freq-xs" y="122">3</text><text class="freq-xs" y="130">1.5</text><text class="freq-xs" y="138">0.75</text>
    <path class="contour" d="M-28,-10 C-32,30 -30,60 -48,76 C-62,90 -80,96 -98,102 C-120,108 -128,124 -132,140"/>
    <path class="contour" d="M22,-10 C30,40 55,70 66,85 C80,100 88,115 88,140"/>
    <circle class="node" cx="-28" cy="-10" r="2"/><circle class="node" cx="-132" cy="140" r="2"/><circle class="node" cx="22" cy="-10" r="2"/><circle class="node" cx="88" cy="140" r="2"/>
    <text class="axis-sm" x="-84" y="152">10µV</text><text class="axis-sm" x="-46.5" y="152">5µV</text><text class="axis-sm" x="-9" y="152">0µV</text><text class="axis-sm" x="9" y="152">0µV</text><text class="axis-sm" x="46.5" y="152">5µV</text><text class="axis-sm" x="84" y="152">10µV</text>
    <text class="axis-name-sm" y="163">sEMG</text>
    <text class="caption" y="184">????</text>
  </g>

  <!-- Superconscious -->
  <g class="pattern pattern-superconscious" transform="translate(418,905)">
    <circle class="halo" cx="0" cy="80" r="60" role="img" aria-label="Brain illustration"/>
    <line class="gridline" x1="-84" y1="8" x2="-84" y2="140"/><line class="gridline" x1="-46.5" y1="8" x2="-46.5" y2="140"/>
    <line class="zero" x1="-9" y1="8" x2="-9" y2="140"/><line class="zero" x1="9" y1="8" x2="9" y2="140"/>
    <line class="gridline" x1="46.5" y1="8" x2="46.5" y2="140"/><line class="gridline" x1="84" y1="8" x2="84" y2="140"/>
    <rect class="g" x="-33" y="13.5" width="24" height="5" rx="2.5"/><rect class="g" x="9" y="13.5" width="24" height="5" rx="2.5"/>
    <rect class="g" x="-33" y="21.5" width="24" height="5" rx="2.5"/><rect class="g" x="9" y="21.5" width="24" height="5" rx="2.5"/>
    <rect class="b1" x="-38" y="29.5" width="29" height="5" rx="2.5"/><rect class="b1" x="9" y="29.5" width="27" height="5" rx="2.5"/>
    <rect class="b1" x="-51" y="37.5" width="42" height="5" rx="2.5"/><rect class="b1" x="9" y="37.5" width="40" height="5" rx="2.5"/>
    <rect class="b2" x="-51" y="45.5" width="42" height="5" rx="2.5"/><rect class="b2" x="9" y="45.5" width="38" height="5" rx="2.5"/>
    <rect class="b3" x="-51" y="53.5" width="42" height="5" rx="2.5"/><rect class="b3" x="9" y="53.5" width="38" height="5" rx="2.5"/>
    <rect class="b4" x="-55" y="61.5" width="46" height="5" rx="2.5"/><rect class="b4" x="9" y="61.5" width="42" height="5" rx="2.5"/>
    <rect class="a2" x="-49" y="69.5" width="40" height="5" rx="2.5"/><rect class="a2" x="9" y="69.5" width="36" height="5" rx="2.5"/>
    <rect class="a2" x="-73" y="77.5" width="64" height="5" rx="2.5"/><rect class="a2" x="9" y="77.5" width="62" height="5" rx="2.5"/>
    <rect class="a3l" x="-40" y="85.5" width="31" height="5" rx="2.5"/><rect class="a3l" x="9" y="85.5" width="31" height="5" rx="2.5"/>
    <rect class="t1" x="-27" y="93.5" width="18" height="5" rx="2.5"/><rect class="t1" x="9" y="93.5" width="18" height="5" rx="2.5"/>
    <rect class="t2" x="-25" y="101.5" width="16" height="5" rx="2.5"/><rect class="t2" x="9" y="101.5" width="16" height="5" rx="2.5"/>
    <rect class="t3" x="-38" y="109.5" width="29" height="5" rx="2.5"/><rect class="t3" x="9" y="109.5" width="31" height="5" rx="2.5"/>
    <rect class="d1" x="-40" y="117.5" width="31" height="5" rx="2.5"/><rect class="d1" x="9" y="117.5" width="31" height="5" rx="2.5"/>
    <rect class="d2" x="-53" y="125.5" width="44" height="5" rx="2.5"/><rect class="d2" x="9" y="125.5" width="44" height="5" rx="2.5"/>
    <rect class="d3" x="-60" y="133.5" width="51" height="5" rx="2.5"/><rect class="d3" x="9" y="133.5" width="49" height="5" rx="2.5"/>
    <text class="freq-xs" y="18">59</text><text class="freq-xs" y="26">49</text><text class="freq-xs" y="34">38</text><text class="freq-xs" y="42">30</text><text class="freq-xs" y="50">24</text><text class="freq-xs" y="58">19</text><text class="freq-xs" y="66">15</text><text class="freq-xs" y="74">12.5</text><text class="freq-xs" y="82">10.5</text><text class="freq-xs" y="90">9</text><text class="freq-xs" y="98">7.5</text><text class="freq-xs" y="106">6</text><text class="freq-xs" y="114">4</text><text class="freq-xs" y="122">3</text><text class="freq-xs" y="130">1.5</text><text class="freq-xs" y="138">0.75</text>
    <path class="contour" d="M-40,10 C-48,36 -52,61 -64,71 C-90,78 -90,88 -64,94 C-52,106 -64,126 -66,140"/>
    <path class="contour" d="M40,10 C48,36 52,61 64,71 C88,78 88,88 64,94 C52,106 64,126 66,140"/>
    <circle class="node" cx="-40" cy="10" r="2"/><circle class="node" cx="-66" cy="140" r="2"/><circle class="node" cx="40" cy="10" r="2"/><circle class="node" cx="66" cy="140" r="2"/>
    <text class="axis-sm" x="-84" y="152">10µV</text><text class="axis-sm" x="-46.5" y="152">5µV</text><text class="axis-sm" x="-9" y="152">0µV</text><text class="axis-sm" x="9" y="152">0µV</text><text class="axis-sm" x="46.5" y="152">5µV</text><text class="axis-sm" x="84" y="152">10µV</text>
    <text class="axis-name-sm" y="163">sEMG</text>
    <text class="caption" y="184">Superconscious</text>
    <text class="caption" y="199">Consciousness</text>
  </g>

  <!-- Universal -->
  <g class="pattern pattern-universal" transform="translate(632,905)">
    <line class="gridline" x1="-84" y1="-8" x2="-84" y2="140"/><line class="gridline" x1="-46.5" y1="-8" x2="-46.5" y2="140"/>
    <line class="zero" x1="-9" y1="-8" x2="-9" y2="140"/><line class="zero" x1="9" y1="-8" x2="9" y2="140"/>
    <line class="gridline" x1="46.5" y1="-8" x2="46.5" y2="140"/><line class="gridline" x1="84" y1="-8" x2="84" y2="140"/>
    <rect class="g" x="-22" y="-2.5" width="13" height="5" rx="2.5"/><rect class="g" x="9" y="-2.5" width="16" height="5" rx="2.5"/>
    <rect class="g" x="-25" y="5.5" width="16" height="5" rx="2.5"/><rect class="g" x="9" y="5.5" width="18" height="5" rx="2.5"/>
    <rect class="g" x="-30" y="13.5" width="21" height="5" rx="2.5"/><rect class="g" x="9" y="13.5" width="24" height="5" rx="2.5"/>
    <rect class="g" x="-39" y="21.5" width="30" height="5" rx="2.5"/><rect class="g" x="9" y="21.5" width="36" height="5" rx="2.5"/>
    <rect class="b1" x="-62" y="29.5" width="53" height="5" rx="2.5"/><rect class="b1" x="9" y="29.5" width="51" height="5" rx="2.5"/>
    <rect class="b1" x="-62" y="37.5" width="53" height="5" rx="2.5"/><rect class="b1" x="9" y="37.5" width="51" height="5" rx="2.5"/>
    <rect class="b2" x="-55" y="45.5" width="46" height="5" rx="2.5"/><rect class="b2" x="9" y="45.5" width="58" height="5" rx="2.5"/>
    <rect class="b3" x="-53" y="53.5" width="44" height="5" rx="2.5"/><rect class="b3" x="9" y="53.5" width="59" height="5" rx="2.5"/>
    <rect class="b4" x="-61" y="61.5" width="52" height="5" rx="2.5"/><rect class="b4" x="9" y="61.5" width="68" height="5" rx="2.5"/>
    <rect class="a2" x="-70" y="69.5" width="61" height="5" rx="2.5"/><rect class="a2" x="9" y="69.5" width="67" height="5" rx="2.5"/>
    <rect class="a2" x="-70" y="77.5" width="61" height="5" rx="2.5"/><rect class="a2" x="9" y="77.5" width="73" height="5" rx="2.5"/>
    <rect class="a3l" x="-71" y="85.5" width="62" height="5" rx="2.5"/><rect class="a3l" x="9" y="85.5" width="73" height="5" rx="2.5"/>
    <rect class="t1" x="-63" y="93.5" width="54" height="5" rx="2.5"/><rect class="t1" x="9" y="93.5" width="51" height="5" rx="2.5"/>
    <rect class="t2" x="-57" y="101.5" width="48" height="5" rx="2.5"/><rect class="t2" x="9" y="101.5" width="44" height="5" rx="2.5"/>
    <rect class="t3" x="-51" y="109.5" width="42" height="5" rx="2.5"/><rect class="t3" x="9" y="109.5" width="42" height="5" rx="2.5"/>
    <rect class="d1" x="-44" y="117.5" width="35" height="5" rx="2.5"/><rect class="d1" x="9" y="117.5" width="45" height="5" rx="2.5"/>
    <rect class="d2" x="-33" y="125.5" width="24" height="5" rx="2.5"/><rect class="d2" x="9" y="125.5" width="17" height="5" rx="2.5"/>
    <rect class="d3" x="-25" y="133.5" width="16" height="5" rx="2.5"/><rect class="d3" x="9" y="133.5" width="23" height="5" rx="2.5"/>
    <text class="freq-xs" y="2">79</text><text class="freq-xs" y="10">69</text><text class="freq-xs" y="18">59</text><text class="freq-xs" y="26">49</text><text class="freq-xs" y="34">38</text><text class="freq-xs" y="42">30</text><text class="freq-xs" y="50">24</text><text class="freq-xs" y="58">19</text><text class="freq-xs" y="66">15</text><text class="freq-xs" y="74">12.5</text><text class="freq-xs" y="82">10.5</text><text class="freq-xs" y="90">9</text><text class="freq-xs" y="98">7.5</text><text class="freq-xs" y="106">6</text><text class="freq-xs" y="114">4</text><text class="freq-xs" y="122">3</text><text class="freq-xs" y="130">1.5</text><text class="freq-xs" y="138">0.75</text>
    <path class="contour" d="M-55,-6 C-110,20 -125,95 -75,140"/>
    <path class="contour" d="M55,-6 C110,20 125,95 80,140"/>
    <circle class="node" cx="-55" cy="-6" r="2"/><circle class="node" cx="-75" cy="140" r="2"/><circle class="node" cx="55" cy="-6" r="2"/><circle class="node" cx="80" cy="140" r="2"/>
    <text class="axis-sm" x="-84" y="152">10µV</text><text class="axis-sm" x="-46.5" y="152">5µV</text><text class="axis-sm" x="-9" y="152">0µV</text><text class="axis-sm" x="9" y="152">0µV</text><text class="axis-sm" x="46.5" y="152">5µV</text><text class="axis-sm" x="84" y="152">10µV</text>
    <text class="axis-name-sm" y="163">sEMG</text>
    <text class="caption" y="184">Universal</text>
    <text class="caption" y="199">Consciousness</text>
  </g>

  <!-- OBE -->
  <g class="pattern pattern-obe" transform="translate(844,905)">
    <circle class="halo" cx="0" cy="72" r="62" role="img" aria-label="Brain illustration"/>
    <line class="gridline" x1="-46.5" y1="-8" x2="-46.5" y2="140"/><line class="zero" x1="-9" y1="-8" x2="-9" y2="140"/>
    <line class="zero" x1="9" y1="-8" x2="9" y2="140"/><line class="gridline" x1="46.5" y1="-8" x2="46.5" y2="140"/>
    <line class="quiet" x1="-10" y1="-4" x2="-10" y2="68"/><line class="quiet" x1="10" y1="-4" x2="10" y2="68"/>
    <rect class="a1" x="-12" y="69.5" width="3" height="5" rx="1.5"/><rect class="a1" x="9" y="69.5" width="3" height="5" rx="1.5"/>
    <rect class="a2" x="-12" y="77.5" width="3" height="5" rx="1.5"/><rect class="a2" x="9" y="77.5" width="3" height="5" rx="1.5"/>
    <rect class="a3l" x="-12" y="85.5" width="3" height="5" rx="1.5"/><rect class="a3l" x="9" y="85.5" width="3" height="5" rx="1.5"/>
    <rect class="t1" x="-12" y="93.5" width="3" height="5" rx="1.5"/><rect class="t1" x="9" y="93.5" width="3" height="5" rx="1.5"/>
    <rect class="t2" x="-12" y="101.5" width="3" height="5" rx="1.5"/><rect class="t2" x="9" y="101.5" width="3" height="5" rx="1.5"/>
    <rect class="t3" x="-12" y="109.5" width="3" height="5" rx="1.5"/><rect class="t3" x="9" y="109.5" width="3" height="5" rx="1.5"/>
    <rect class="d1" x="-14" y="117.5" width="5" height="5" rx="2.5"/><rect class="d1" x="9" y="117.5" width="7" height="5" rx="2.5"/>
    <rect class="d2" x="-22" y="125.5" width="13" height="5" rx="2.5"/><rect class="d2" x="9" y="125.5" width="12" height="5" rx="2.5"/>
    <rect class="d3" x="-25" y="133.5" width="16" height="5" rx="2.5"/><rect class="d3" x="9" y="133.5" width="13" height="5" rx="2.5"/>
    <text class="freq-xs" y="2">79</text><text class="freq-xs" y="10">69</text><text class="freq-xs" y="18">59</text><text class="freq-xs" y="26">49</text><text class="freq-xs" y="34">38</text><text class="freq-xs" y="42">30</text><text class="freq-xs" y="50">24</text><text class="freq-xs" y="58">19</text><text class="freq-xs" y="66">15</text><text class="freq-xs" y="74">12.5</text><text class="freq-xs" y="82">10.5</text><text class="freq-xs" y="90">9</text><text class="freq-xs" y="98">7.5</text><text class="freq-xs" y="106">6</text><text class="freq-xs" y="114">4</text><text class="freq-xs" y="122">3</text><text class="freq-xs" y="130">1.5</text><text class="freq-xs" y="138">0.75</text>
    <path class="contour" d="M-32,-6 C-32,60 -34,110 -44,142"/>
    <path class="contour" d="M28,-6 C28,60 30,110 38,142"/>
    <circle class="node" cx="-32" cy="-6" r="2"/><circle class="node" cx="-44" cy="142" r="2"/><circle class="node" cx="28" cy="-6" r="2"/><circle class="node" cx="38" cy="142" r="2"/>
    <text class="axis-sm" x="-46.5" y="152">5µV</text><text class="axis-sm" x="-9" y="152">0µV</text><text class="axis-sm" x="9" y="152">0µV</text><text class="axis-sm" x="46.5" y="152">5µV</text>
    <text class="axis-name-sm" y="163">sEMG</text>
    <text class="caption" y="184">OBE (Out of Body)</text>
  </g>
</svg>
</body>
</html>
```